Brenwick Structures Construction Company Seeking Modern Website

We are a small construction company wanting to create a web presence. We don't have much in the way of current content but will get photos as they come in. Attached is a picture of our business card.
The pages we would like on the menu are:
Home
Portfolio
Product Specs
Testimonials
Our Process
Contact
Some designs we like are:
http://www.tovasheds-example.com/
http://www.qrnstructures-example.com/
http://dunholtbarns-example.com/
http://pellingframes-example.com/
Not much requirements other than that so feel free to be creative!
Updates
Target Market(s)
Construction
Commercial and Residential Buildings
Industry/Entity Type
Construction Company
Number of Pages Required
5+ page
Look and feel

```html
<!DOCTYPE html>
<html lang="en">
<head>
<meta charset="utf-8">
<title>Brenwick Structures</title>
<link href="https://fonts.googleapis.com/css2?family=Lato:ital,wght@0,400;0,700;1,400&family=Fjalla+One&family=Berkshire+Swash&display=swap" rel="stylesheet">
<style>
:root{
  --blue:#1a9ad6;
  --blue-dark:#1280b5;
  --band:#2196cc;
  --dark:#353535;
  --footer:#3a3a3a;
  --red:#d7261e;
  --text:#555;
  --light:#f4f4f4;
}
*{margin:0;padding:0;box-sizing:border-box}
html,body{width:768px;height:1200px;overflow:hidden}
body{font-family:'Lato',sans-serif;color:var(--text);position:relative;background:#fff}
.abs{position:absolute}
.topbar{left:0;top:0;width:768px;height:24px;background:var(--blue)}
.lang{left:84px;top:5px;height:14px;width:48px;border:1px solid rgba(255,255,255,.5);color:#fff;font-size:8px;line-height:12px;padding-left:4px}
.social{left:562px;top:0;height:24px;display:flex}
.social span{width:24.5px;height:24px;background:var(--blue-dark);border-left:1px solid var(--blue);display:flex;align-items:center;justify-content:center}
.social i{display:block;width:8px;height:8px;background:#fff;border-radius:2px}
.header{left:0;top:24px;width:768px;height:60px;background:#fff}
.brand{left:84px;top:42px;display:flex;align-items:center;gap:8px;font-size:22px;font-weight:700;color:var(--blue)}
.brand b{width:18px;height:18px;background:var(--red);border-radius:50%}
.call{right:84px;top:46px;font-size:13px;color:#666;font-style:italic;display:flex;align-items:center;gap:10px}
.call em{font-style:normal;color:var(--blue);display:flex;align-items:center;gap:4px}
.nav{left:0;top:84px;width:768px;height:30px;background:var(--dark)}
.nav ul{list-style:none;display:flex;margin-left:84px}
.nav li{width:100px;height:30px;line-height:30px;text-align:center;color:#fff;font-size:9.5px;border-right:1px solid #444}
.nav li.on{background:var(--blue)}
.hero{left:0;top:114px;width:768px;height:330px;background:linear-gradient(160deg,#cfd9e3 0%,#8fa1b3 30%,#e5c9b2 55%,#6f7480 75%,#b9866d 100%)}
.hero h1{position:absolute;left:0;width:768px;top:32px;text-align:center;font-family:'Fjalla One',sans-serif;font-weight:400;font-size:27px;line-height:34px;color:var(--blue)}
.welcome{left:0;top:332px;width:768px;height:112px;background:rgba(25,150,205,.85);color:#fff;text-align:center}
.welcome h2{font-weight:400;font-size:19px;margin-top:14px;letter-spacing:.5px}
.welcome .rule{width:240px;height:1px;background:rgba(255,255,255,.7);margin:5px auto 0;position:relative}
.welcome .rule:after{content:"";position:absolute;left:110px;top:0;border:10px solid transparent;border-top:8px solid #fff;border-bottom:0}
.welcome p{font-size:9px;line-height:13.5px;width:580px;margin:11px auto 0}
.plus{left:368px;top:428px;width:32px;height:16px;background:var(--dark);color:#fff;text-align:center;font-size:15px;line-height:16px;font-weight:700}
.card{width:185px;height:194px;top:490px;background:#fff;border:1px solid #ddd;border-top:2px solid var(--dark);box-shadow:0 6px 6px -4px rgba(0,0,0,.15)}
.pill{height:30px;width:120px;background:var(--red);border:2px solid #8e1410;border-radius:50%;color:#fff;font-family:'Berkshire Swash',cursive;font-size:15px;text-align:center;line-height:26px}
.card .pill{position:absolute;left:32px;top:-16px}
.photo{background:linear-gradient(135deg,#d9b9a0,#c89a7d 50,#e8e2da);border:1px solid #999}
.about .photo{position:absolute;left:8px;top:34px;width:170px;height:73px;background:linear-gradient(135deg,#e7d8ca,#c99577,#eee)}
.card p.body{position:absolute;left:9px;top:118px;width:168px;font-size:8px;line-height:12.6px}
.more{position:absolute;right:8px;bottom:10px;color:var(--blue);font-size:8px;font-weight:700;display:flex;align-items:center;gap:3px}
.more i{width:8px;height:8px;border-radius:50%;background:#666;color:#fff;font-style:normal;font-size:8px;line-height:8px;text-align:center}
.item{position:absolute;left:8px;width:170px}
.item h4{font-size:10px;font-weight:400;color:#333;padding-left:17px;position:relative}
.item h4 svg{position:absolute;left:0;top:2px}
.item p{font-size:8px;line-height:12.6px;padding-left:17px;margin-top:3px}
.item .more{position:static;justify-content:flex-end;margin-top:2px}
.news{position:absolute;left:9px;width:167px;display:flex;gap:8px;padding-bottom:6px;border-bottom:1px dotted #aaa}
.date{width:24px;height:24px;border:1px solid var(--blue);text-align:center;font-size:9px;line-height:12px;color:#555;flex:none}
.date span{display:block;background:var(--blue);color:#fff;font-size:6px;line-height:10px}
.news h5{font-size:7.6px;font-weight:400;color:#333}
.news p{font-size:7.4px;line-height:11.3px}
.types-line{left:84px;top:747px;width:600px;height:2px;background:var(--dark)}
.types{left:0;top:748px;width:768px;height:162px;background:var(--band)}
.types .pill{position:absolute;left:324px;top:-14px}
.tile{top:32px;height:102px;border:2px solid #fff;background:linear-gradient(180deg,#cfd4d8,#8c9196 60%,#b6aa8e)}
.tile span{position:absolute;left:0;right:0;bottom:0;height:18px;background:rgba(255,255,255,.75);text-align:center;font-size:10px;line-height:18px;color:#333;font-weight:700}
.arrow{top:82px}
.say{left:0;top:942px;width:768px;text-align:center}
.say h3{color:var(--red);font-weight:400;font-size:20px}
.say p{color:#666;font-size:15px;margin-top:2px}
.quote{left:84px;top:1002px;width:512px;height:64px;border:1px solid #ddd;box-shadow:0 2px 4px rgba(0,0,0,.08);font-style:italic;font-size:8.3px;line-height:15px;padding:9px 12px;color:#333}
.quote:after{content:"";position:absolute;left:456px;bottom:-8px;border:8px solid transparent;border-top-color:#ddd;border-bottom:0}
.avatar{left:598px;top:998px;width:76px;height:76px;border-radius:50%;background:radial-gradient(circle at 50% 45%,#d6b7a0,#8f6d57 60%,#dfe3e7 62%);border:4px solid #eee;box-shadow:0 2px 5px rgba(0,0,0,.25)}
.who{right:160px;top:1083px;font-size:8px;font-style:italic;font-weight:700;color:#333}
.footer{left:0;top:1122px;width:768px;height:74px;background:var(--footer)}
.fnav{position:absolute;left:84px;top:28px;display:flex;list-style:none}
.fnav li{font-size:7.5px;color:#fff;padding:0 7px;border-right:1px solid #555}
.fnav li:first-child{padding-left:2px;color:var(--blue)}
.fnav li:last-child{border:0}
.fbrand{position:absolute;left:496px;top:19px;display:flex;align-items:center;gap:6px}
.fbrand .c{width:24px;height:24px;border-radius:50%;background:var(--blue);display:flex;align-items:center;justify-content:center}
.fbrand .c2{background:#666}
.fbrand strong{font-size:18px;color:#888;margin-left:4px}
.copy{position:absolute;right:84px;top:57px;font-size:8px;color:#ddd}
.base{left:0;top:1196px;width:768px;height:4px;background:var(--blue)}
</style>
</head>
<body>
<div class="abs topbar"></div>
<div class="abs lang">English &#8964;</div>
<div class="abs social">
  <span><svg width="10" height="10" viewBox="0 0 10 10"><circle cx="4" cy="4" r="3" fill="none" stroke="#fff" stroke-width="1.4"/><line x1="6.2" y1="6.2" x2="9" y2="9" stroke="#fff" stroke-width="1.5"/></svg></span>
  <span><i></i></span><span><i></i></span><span><i></i></span><span><i></i></span>
</div>

<div class="abs header"></div>
<div class="abs brand"><b></b>Brenwick Structures</div>
<div class="abs call">Call us TODAY !
  <em><svg width="11" height="11" viewBox="0 0 24 24"><path fill="#1a9ad6" d="M6.6 10.8a15 15 0 0 0 6.6 6.6l2.2-2.2a1 1 0 0 1 1-.25 11.4 11.4 0 0 0 3.6.57 1 1 0 0 1 1 1V20a1 1 0 0 1-1 1A17 17 0 0 1 3 4a1 1 0 0 1 1-1h3.5a1 1 0 0 1 1 1c0 1.25.2 2.45.57 3.57a1 1 0 0 1-.25 1z"/></svg>+123 456 7890</em>
</div>

<nav class="abs nav"><ul>
  <li class="on">HOME</li><li>PORTFOLIO</li><li>PRODUCT SPECS</li><li>TESTIMONIALS</li><li>OUR PROCESS</li><li>CONTACT US</li>
</ul></nav>

<section class="abs hero" role="img" aria-label="Two businessmen shaking hands in front of glass office towers">
  <h1>Building Dreams, So You Can<br>Build Memories</h1>
</section>
<section class="abs welcome">
  <h2>WELCOME TO BRENWICK STRUCTURES</h2>
  <div class="rule"></div>
  <p>Lorem ipsum dolor sit amet, consectetur adipiscing elit. Praesent volutpat ultricies euismod. Mauris consectetur tellus quis sem dictum pharetra. Nullam euismod nunc blandit mi sagittis, et posuere nunc iaculis. Aenean in sollicitudin quam, non accumsan ipsum. Vivamus in aliquet ex. Nullam malesuadammodo mi, tristique faucibus nisl condimentum condimentum. Duis porttitor nisi ut elementum so</p>
</section>
<div class="abs plus">+</div>

<article class="abs card about" style="left:84px">
  <div class="pill">About Us</div>
  <div class="photo" role="img" aria-label="Team members stacking their hands together"></div>
  <p class="body">Hendrerit in vulputate molestie consquat, sisi atvero eros et accumsan iustoodio dignissimr qui blandit praesent luptatulenit auedolore te feugait nulla facilisilestie conseyat,</p>
  <div class="more">READ MORE <i>+</i></div>
</article>

<article class="abs card" style="left:292px">
  <div class="pill">What We Do</div>
  <div class="item" style="top:34px">
    <h4><svg width="10" height="8" viewBox="0 0 10 8"><path d="M1 4l3 3 5-6" fill="none" stroke="#3a9d8f" stroke-width="2"/></svg>Vulputate Molestie Consequat</h4>
    <p>quis nostrud exsetiperj aliquip commod consequa uisquis nostru suscipit nisl roli aliquip exea commod</p>
    <div class="more">KNOW MORE</div>
  </div>
  <div style="position:absolute;left:10px;top:106px;width:165px;border-top:1px dashed #aaa"></div>
  <div class="item" style="top:112px">
    <h4><svg width="10" height="8" viewBox="0 0 10 8"><path d="M1 4l3 3 5-6" fill="none" stroke="#3a9d8f" stroke-width="2"/></svg>Vulputate Molestie Consequat</h4>
    <p>quis nostrud exetiperj saliquip commodr consequa uisquis nostru iexetip suscipitt lobtis nisl ut aliquip exea commod</p>
    <div class="more">KNOW MORE</div>
  </div>
</article>

<article class="abs card" style="left:500px">
  <div class="pill">Latest News</div>
  <div class="news" style="top:36px"><div class="date">25<span>NOV</span></div><div><h5>Vero eros accumsaet odio</h5><p>quis nostrud exetiperj suscipit lobtis nisl ut aliquip ex ea commod</p></div></div>
  <div class="news" style="top:82px"><div class="date">22<span>NOV</span></div><div><h5>Eros accumsaet iusto odio</h5><p>quis nostrud exetiperj suscipit lobtfis nisl ut aliquip exea commod</p></div></div>
  <div class="news" style="top:129px;border:0"><div class="date">20<span>NOV</span></div><div><h5>Croeros accumsaet iusto odio</h5><p>quis nostrud exetiperj suscipit lobtisf nisl ut aliquip ex commod</p></div></div>
  <div class="more">READ MORE <i>+</i></div>
</article>

<div class="abs types-line"></div>
<section class="abs types">
  <div class="pill">Building Types</div>
  <svg class="abs arrow" style="left:68px" width="10" height="16" viewBox="0 0 10 16"><path d="M8 1L2 8l6 7" fill="none" stroke="#7cc3e6" stroke-width="2"/></svg>
  <div class="abs tile" style="left:85px;width:145px" role="img" aria-label="Farm shop buildings"><span>Farm Shops</span></div>
  <div class="abs tile" style="left:236px;width:145px" role="img" aria-label="Machine storage shed"><span>Machine Storage</span></div>
  <div class="abs tile" style="left:387px;width:145px" role="img" aria-label="Seed dealership with grain silos"><span>Seed Dealership</span></div>
  <div class="abs tile" style="left:538px;width:146px" role="img" aria-label="Dairy barn from above"><span>Dairy</span></div>
  <svg class="abs arrow" style="left:690px" width="10" height="16" viewBox="0 0 10 16"><path d="M2 1l6 7-6 7" fill="none" stroke="#e8563a" stroke-width="2"/></svg>
</section>

<section class="abs say">
  <h3>What Our Customers Say</h3>
  <p>Lorem ipsum dolor sit amet consectetur Donec a consequat mag</p>
</section>
<blockquote class="abs quote">&nbsp;&nbsp;&nbsp;&nbsp;&nbsp;&nbsp;&nbsp;Lorem sum dolor sit amet, consectetuer adipiscing elit, sed diam nonummy nibh euismod tincidunt ut laoreet re agn aliqam erat volutpat wisi enim ad minim veniam, quis nostrud exerci tation ullamcorper suscipit lobortis nisl ut aliquip modo conseuatis autem vel eum iriure dolor in hendrerit in vulputate velit esse molestie consequat, vel illum dolore eu.</blockquote>
<div class="abs avatar" role="img" aria-label="Customer portrait"></div>
<div class="abs who">Daniel Mora, Halvek Group, USA</div>

<footer class="abs footer">
  <ul class="fnav"><li>HOME</li><li>PORTFOLIO</li><li>PRODUCT SPACS</li><li>TESTIMONIALS</li><li>OUR PROCESS</li><li>CONTACT US</li></ul>
  <div class="fbrand">
    <span class="c"><svg width="9" height="13" viewBox="0 0 9 13"><rect x=".8" y=".8" width="7.4" height="11.4" rx="1" fill="none" stroke="#fff" stroke-width="1.3"/><circle cx="4.5" cy="10" r=".8" fill="#fff"/></svg></span>
    <span class="c c2"><svg width="13" height="9" viewBox="0 0 13 9"><rect x=".6" y=".6" width="11.8" height="7.8" fill="none" stroke="#fff" stroke-width="1.2"/><path d="M.6 .6l5.9 4.5 5.9-4.5" fill="none" stroke="#fff" stroke-width="1.2"/></svg></span>
    <strong>Brenwick Structures</strong>
  </div>
  <div class="copy">Copyright © 2015 Brenwick Structures &nbsp;|&nbsp; All Rights Reserved</div>
</footer>
<div class="abs base"></div>
</body>
</html>
```